kmvalerohub website

I need a new homepage design for my current website at www.KMValeroHub.com. I want someone to look at my current website and develop a more appealing homepage... right now the colors don't blend very well and it needs a facelift

Reason: This has been extended to September 10th

```html
<!DOCTYPE html>
<html lang="en">
<head>
<meta charset="utf-8">
<title>KM Valero – Home</title>
<link rel="stylesheet" href="https://fonts.googleapis.com/css2?family=Open+Sans:wght@400;600;700&family=Roboto+Slab:wght@500;700&family=Oswald:wght@500;700&family=Dancing+Script:wght@700&display=swap">
<style>
:root{
  --brand-red:#b3202a;
  --brand-red-bright:#d0282f;
  --ink:#2a2a2c;
  --text:#4a4a4a;
  --page:#dcdcdc;
  --white:#ffffff;
  --green-deep:#2f7d1f;
  --green-light:#d9f6cf;
  --blue-badge:#1f6f96;
}
*{margin:0;padding:0;box-sizing:border-box}
html,body{width:889px;height:1200px;overflow:hidden}
body{background:var(--page);font-family:"Open Sans",Arial,sans-serif;color:var(--text);position:relative}
.site-header{position:absolute;left:0;top:0;width:889px;height:66px;background:var(--brand-red)}
.brand{position:absolute;left:75px;top:18px;color:var(--white);font:700 22px "Oswald",Arial,sans-serif;letter-spacing:2px}
.social{position:absolute;display:flex;gap:9px}
.social span{width:23px;height:23px;border-radius:50%;background:var(--white);display:block}
.header-social{right:82px;top:21px}
.main-nav{position:absolute;left:75px;top:66px;width:740px;height:37px;background:var(--ink);display:flex}
.main-nav a{color:#e6e6e6;text-decoration:none;font-size:11.5px;letter-spacing:.6px;line-height:37px;padding:0 21px;position:relative}
.main-nav a.active{color:var(--brand-red-bright);padding:0 27px}
.main-nav a.active::after{content:"";position:absolute;left:0;right:0;bottom:0;height:3px;background:var(--brand-red-bright)}
.main-nav a:nth-child(2){padding-left:21px}
.hero{position:absolute;left:76px;top:110px;width:737px;height:312px;background:linear-gradient(90deg,#e9e4e1 0%,#f3efec 45%,#e6dcd6 100%)}
.hero-photo{position:absolute;left:110px;top:0;width:180px;height:312px;background:linear-gradient(180deg,#6b4a3c 0%,#3a3537 40%,#2f2c2e 100%);border-radius:60px 60px 0 0}
.hero-tag{position:absolute;left:401px;top:74px;width:149px;height:32px;background:var(--brand-red);color:var(--white);font:700 16px "Open Sans",sans-serif;letter-spacing:1.5px;text-align:center;line-height:32px}
.hero-panel{position:absolute;left:325px;top:105px;width:300px;height:101px;background:var(--ink);text-align:center;padding-top:13px}
.hero-panel .lead{color:var(--white);font-size:13.5px;letter-spacing:1px}
.hero-panel .big{color:var(--brand-red-bright);font-size:22px;letter-spacing:2px;line-height:27px}
.hero-panel .big b{color:var(--white);font-weight:400}
.arrow{position:absolute;top:138px;width:24px;height:24px;border-radius:50%}
.arrow.prev{left:33px;background:var(--brand-red)}
.arrow.next{right:28px;background:#a9a9a9}
.arrow svg{display:block}
.rule{position:absolute;left:0;top:433px;width:889px;height:1px;background:#c7c7c7}
.dots{position:absolute;left:416px;top:430px;width:58px;height:15px;background:var(--page);border:1px solid #c7c7c7;border-top:none;display:flex;justify-content:center;align-items:center;gap:3px}
.dots i{width:5px;height:5px;border-radius:50%;border:1px solid #999;display:block}
.dots i.on{background:var(--brand-red);border-color:var(--brand-red)}
.section-title{position:absolute;color:var(--brand-red);font:600 13.5px "Open Sans",sans-serif}
.about-title{left:75px;top:476px}
.about-photo{position:absolute;left:75px;top:505px;width:108px;height:135px;background:linear-gradient(180deg,#8a8a8a,#3b3b3b)}
.about-text{position:absolute;font-size:9.4px;line-height:14px;text-align:justify}
.about-text.side{left:200px;top:503px;width:265px}
.about-text.full{left:73px;top:650px;width:392px}
.news-title{left:504px;top:478px}
.news-box{position:absolute;left:505px;top:507px;width:309px;height:180px;background:var(--white);border:1px solid #cfcfcf;border-radius:3px}
.news-icon{position:absolute;left:475px;top:520px;width:62px;height:62px;border-radius:50%;background:#c9c9c9;display:flex;align-items:center;justify-content:center}
.news-icon span{width:50px;height:50px;border-radius:50%;background:var(--brand-red);display:flex;align-items:center;justify-content:center}
.news-copy{position:absolute;left:42px;top:36px;width:250px;font-size:8px;line-height:11px;color:#777}
.field{position:absolute;top:79px;width:115px;height:20px;border:1px solid #cfcfcf;font-size:8px;color:#666;padding:5px 7px}
.field.name{left:42px}.field.email{left:164px}
.check{position:absolute;left:43px;top:121px;font-size:7.5px;color:#666;display:flex;align-items:center;gap:6px}
.check i{width:10px;height:10px;border:1px solid #bbb;display:block}
.subscribe{position:absolute;left:187px;top:113px;width:90px;height:22px;background:var(--brand-red);color:var(--white);font-size:11.5px;display:flex;align-items:center;justify-content:center;gap:6px}
.subscribe i{width:11px;height:11px;border-radius:50%;background:var(--white);display:block}
.promo{position:absolute;left:75px;top:737px;width:740px;height:211px;background:linear-gradient(90deg,#dff6d2 0%,#f0fbe6 55%,#b9ecd5 100%)}
.promo-title{position:absolute;left:67px;top:22px;color:var(--green-deep);font:700 38px "Oswald",sans-serif;line-height:42px}
.promo-title small{display:block;color:#1e6d87;font:500 26px "Open Sans",sans-serif;letter-spacing:10px;line-height:30px}
.promo-script{position:absolute;left:225px;top:4px;color:#4caa2c;font:700 44px "Dancing Script",cursive}
.promo-tagline{position:absolute;left:66px;top:163px;color:#2d6a1c;font:700 16px "Oswald",sans-serif}
.promo-avail{position:absolute;left:421px;top:163px;color:#1e6d87;font:700 17px "Dancing Script",cursive}
.promo-byline{position:absolute;left:145px;top:187px;color:#3e9a2a;font-size:12px}
.badge{position:absolute;left:426px;top:42px;width:102px;height:102px;border-radius:50%;background:var(--blue-badge);color:var(--white);text-align:center;font:500 14px "Oswald",sans-serif;line-height:18px;padding-top:24px}
.book{position:absolute;left:545px;top:10px;width:125px;height:180px;background:linear-gradient(180deg,#e7f3e1,#6bb04a 60%,#2d6f8c);transform:rotate(8deg)}
.seen-title{position:absolute;left:0;width:889px;top:990px;text-align:center;color:var(--brand-red);font:700 13px "Roboto Slab",serif}
.seen-row{position:absolute;left:75px;top:1031px;display:flex;gap:25px}
.seen-row span{width:103px;height:61px;background:var(--white);display:flex;align-items:center;justify-content:center;font:700 11.5px "Open Sans",sans-serif;color:var(--ink)}
.site-footer{position:absolute;left:0;top:1130px;width:889px;height:70px;background:var(--ink)}
.footer-links{position:absolute;left:75px;top:21px;display:flex;gap:10px;font-size:9.5px;color:var(--white)}
.copyright{position:absolute;left:75px;top:41px;font-size:9.5px;color:var(--white)}
.footer-social{right:83px;top:24px}
</style>
</head>
<body>
<header class="site-header">
  <div class="brand">KM VALERO</div>
  <div class="social header-social"><span></span><span></span><span></span></div>
</header>
<nav class="main-nav">
  <a class="active" href="#">HOME</a><a href="#">PRODUCTS</a><a href="#">ABOUT</a><a href="#">BLOG</a><a href="#">FORUM</a><a href="#">MEDIA ROOM</a><a href="#">SUCCESS STORIES</a>
</nav>
<section class="hero">
  <div class="hero-photo" role="img" aria-label="Portrait of KM Valero in a dark dress"></div>
  <div class="hero-tag">KM VALERO</div>
  <div class="hero-panel">
    <div class="lead">DISCOVER SECRET TO A</div>
    <div class="big">SLIMER SEXIER</div>
    <div class="big"><b>&amp;</b>HEALTHIER YOU</div>
  </div>
  <span class="arrow prev"><svg width="24" height="24"><path d="M14 7l-5 5 5 5" stroke="#fff" stroke-width="2.5" fill="none"/></svg></span>
  <span class="arrow next"><svg width="24" height="24"><path d="M10 7l5 5-5 5" stroke="#fff" stroke-width="2.5" fill="none"/></svg></span>
</section>
<div class="rule"></div>
<div class="dots"><i class="on"></i><i></i><i></i><i></i><i></i></div>

<h2 class="section-title about-title">About KM Valero</h2>
<div class="about-photo" role="img" aria-label="Black and white portrait of KM Valero"></div>
<p class="about-text side">KM Valero is a nutritionist and certified weight-loss expert, passionate relationship/life coach, and inspirational speaker. She has been featured on The Daybreak Hour, The Open Table Show, Late Lights, and The City Talk Show. KM has made appearances on several national television stations, as well as in the pages of Lumen, Bloom, Vital and Home Circle. Since reclaiming her health, losing weight, and discovering a “second youth” in her forties, bestselling author KM Valero has</p>
<p class="about-text full">become the voice of inspiration to women who want to lose weight, be healthy, and get their sexy back! KM Valero provides lifestyle solutions for losing weight, getting healthy, looking younger and improving your love life!</p>

<h2 class="section-title news-title">Subscribe to our Newsletter</h2>
<div class="news-box">
  <p class="news-copy">Lorem Ipsum is simply dummy text of the printing and typesetting industry. Lorem Ipsum has been the industry's standard dummy text ever since the 1500s, when an unknown printer took</p>
  <div class="field name">Name</div>
  <div class="field email">email address</div>
  <div class="check"><i></i>Daily Newsletter</div>
  <div class="subscribe"><i></i>Subscribe</div>
</div>
<div class="news-icon"><span><svg width="30" height="22" viewBox="0 0 30 22"><rect x="1" y="1" width="28" height="20" fill="none" stroke="#fff" stroke-width="2"/><path d="M1 1l14 11L29 1M1 21l10-9M29 21l-10-9" stroke="#fff" stroke-width="2" fill="none"/></svg></span></div>

<section class="promo">
  <div class="promo-title">7-DAY VERDE<br>BLEND RESET<small>RESET</small></div>
  <div class="badge">LOSE UP TO<br>15 POUNDS<br>IN 10 DAYS!</div>
  <div class="book" role="img" aria-label="Book cover with green smoothie and vegetables"></div>
  <div class="promo-tagline">LOSE WEIGHT. GET HEALTHY. FEEL ENERGIZED.</div>
  <div class="promo-avail">Available Now</div>
  <div class="promo-byline">By KM Valero, #1 Bestselling Author, Nutritionist and Weight-Loss Expert</div>
</section>

<h2 class="seen-title">As Seen On...</h2>
<div class="seen-row">
  <span>Channel 9</span><span>Home Circle</span><span>Lumen</span><span>Network Five</span><span>Orbit Radio</span><span>Pulse 104</span>
</div>

<footer class="site-footer">
  <div class="footer-links"><span>Contact Us</span><span>Privacy &amp; Security</span><span>Terms of Use</span><span>Opt-out</span></div>
  <div class="copyright">Copyright 2014 kmvalerohub.com All Rights Rights Reserved</div>
  <div class="social footer-social"><span></span><span></span><span></span><span></span><span></span></div>
</footer>
</body>
</html>
```